Inspection Company - Commercial Brochure Design

We are looking to finalize our 8 x 11 brochure. We are an industry leader in our space of commercial and home inspections.

We really like the front and back design labeled-

We have made some suggestions for the internal pages-

These are only suggestions for the interior section- The wording should remain the same. The images can be removed / rearranged/ etc. There is full creative freedom for the interior.

Wording for Inside Right Page-
With over 500,000 properties inspected we know how to inspect each building type to maximize a Return On Investment for our clients. . Our Inspectors focus on all the critical building components (structural, roof, electrical, plumbing, air and heating, drainage, etc.), health and safety issues – emergency egress and other potential hazards. We document current condition and any immediate and future repairs that are necessary. When scheduling our team take all details into account building construction type, age, location, and property use into consideration to ensure we are fully prepared to conduct a thorough inspection.

Target Market(s)

Investors- Commercial Real Estate Investors

Industry/Entity Type

Commercial Real Estate Inspections

Requirements
Must have
• Similar branding to our website (https://morvanteq.com/brightcommercial) (https://bravuraassessments.com/) and ( the uploaded documents (Commercial report cover sample.JPG & designcrowd_z6se15j73jk0fe9fc2samkecn7_image (1).jpg )
Nice to have
• Must have Brand Logos and Brand Colors- Nice to have creative ideas of displaying the information

```html
<!DOCTYPE html>
<html lang="en">
<head>
<meta charset="utf-8">
<title>Bravura Group – Commercial Inspection Brochure</title>
<link rel="stylesheet" href="https://fonts.googleapis.com/css2?family=Arimo:wght@400;700&family=Open+Sans:wght@300;400&display=swap">
<style>
  :root {
    --backdrop: #d2d2d2;
    --navy-deep: #0b2a4e;
    --navy-mid: #123f6e;
    --blue-band: #1a5a95;
    --heading-blue: #1f5fa0;
    --sheet-blue: #3c7fc4;
    --sky: #8cc6ee;
    --panel-grey: #e7e7e7;
    --line-grey: #b9c2cc;
    --ink: #1c1c1c;
    --white: #ffffff;
  }
  * { margin: 0; padding: 0; box-sizing: border-box; }
  html, body { width: 1200px; height: 719px; overflow: hidden; background: var(--backdrop); }
  body { position: relative; font-family: "Arimo", Arial, sans-serif; }

  .page { position: absolute; background: var(--white); overflow: hidden; }
  .page--cover { left: 26px; top: 19px; width: 507px; height: 653px; }
  .page--inspect { left: 664px; top: 19px; width: 511px; height: 656px; }

  .header-band {
    position: absolute; left: 0; top: 20px; width: 100%; height: 156px;
    background: linear-gradient(180deg, var(--navy-deep) 0%, var(--navy-mid) 55%, var(--blue-band) 100%);
  }
  .footer-band {
    position: absolute; left: 0; bottom: 0; width: 100%; height: 152px; overflow: hidden;
    background: linear-gradient(180deg, var(--navy-deep) 0%, var(--navy-mid) 50%, var(--blue-band) 100%);
  }
  .footer-ring {
    position: absolute; left: 31px; top: -28px; width: 152px; height: 152px;
    border: 6px solid rgba(255,255,255,0.18); border-radius: 50%;
  }

  .brand { position: absolute; left: 32px; top: 14px; display: flex; align-items: center; gap: 8px; }
  .brand__mark { width: 58px; height: 58px; border: 3px solid var(--white); border-radius: 50%; }
  .brand__name { color: var(--white); font-weight: 700; font-size: 17px; letter-spacing: 0.5px; }

  .cover-title {
    position: absolute; left: 96px; top: 79px; color: var(--white);
    font-size: 20px; line-height: 31px; font-weight: 400; letter-spacing: 0.2px;
  }

  /* report mock-ups */
  .sheet { position: absolute; background: var(--white); border: 2px solid var(--sheet-blue);
    box-shadow: 2px 3px 6px rgba(0,0,0,0.2); padding: 0 6px; }
  .sheet--back { left: 76px; top: 284px; width: 144px; height: 186px; border-color: #6da6dc; }
  .sheet--front { left: 198px; top: 222px; width: 157px; height: 205px; }
  .sheet__bar { height: 10px; margin: 0 -6px 5px; background: var(--sheet-blue); }
  .sheet--back .sheet__bar { background: #6da6dc; }
  .photo-grid { display: grid; grid-template-columns: repeat(3, 1fr); gap: 3px 3px; }
  .photo-grid__cell { height: 30px; background: linear-gradient(135deg, #c3c6c8, #7f8589); }
  .photo-grid__caption { height: 10px; border-top: 2px solid var(--line-grey); border-bottom: 2px solid var(--line-grey); margin: 2px 6px 0; }
  .text-lines span { display: block; height: 2px; margin: 3px 0; background: var(--line-grey); }
  .text-lines span.warn { background: #e07c7c; }
  .text-lines__head { height: 4px; margin: 5px 0 3px; background: var(--sheet-blue); }

  .phone { position: absolute; left: 323px; top: 194px; width: 108px; height: 224px; border-radius: 14px;
    background: #1e1e1e; box-shadow: 2px 4px 8px rgba(0,0,0,0.35); }
  .phone__screen { position: absolute; left: 6px; top: 26px; width: 96px; height: 168px;
    background: linear-gradient(180deg, #ffffff 0%, #ffffff 18%, #7b8fb5 30%, #4b5f87 52%, #e9eef5 58%, #1b4a80 62%, #123a6a 100%); }
  .phone__button { position: absolute; left: 46px; top: 200px; width: 16px; height: 16px; border: 2px solid #555; border-radius: 50%; }

  .site-url {
    position: absolute; right: 35px; bottom: 28px; font-family: "Open Sans", Arial, sans-serif;
    font-weight: 300; font-size: 13px; letter-spacing: 1.2px; color: var(--white);
  }

  .inspect-title { position: absolute; left: 96px; top: 66px; color: var(--white); font-size: 20px; font-weight: 400; }
  .inspect-intro {
    position: absolute; left: 96px; top: 92px; width: 408px; color: var(--white);
    font-size: 10.6px; line-height: 11.9px;
  }

  .photo { position: absolute; border-radius: 12px; border: 3px solid var(--white);
    box-shadow: 0 -3px 0 var(--sky), 3px 4px 6px rgba(0,0,0,0.3); }
  .photo--wall { background: linear-gradient(135deg, #b7b0a2, #6d6457); }
  .photo--meter { background: linear-gradient(135deg, #d9cfc0, #7a6a52); }
  .photo--drain { background: linear-gradient(135deg, #9aa39a, #5f6760); }
  .photo--thermal { background: linear-gradient(135deg, #c9c9c9, #3a3a3a); }

  .category-title { position: absolute; color: var(--heading-blue); font-size: 19px; font-weight: 400;
    transform: translateX(-50%); white-space: nowrap; }

  .item-panel { position: absolute; background: var(--panel-grey); border-radius: 6px; }
  .item-list { position: absolute; list-style: none; color: var(--ink); }
  .item-list li { position: relative; }
  .item-list--plain { font-size: 11.5px; line-height: 16px; }
  .item-list--dashed li.has-dash::before {
    content: ""; position: absolute; left: -21px; top: 5px; width: 15px; height: 3px; background: var(--heading-blue);
  }
  .item-list--roof { font-size: 9.8px; line-height: 14.7px; }
  .item-list--foundation { font-size: 11.3px; line-height: 16px; }
</style>
</head>
<body>

<section class="page page--cover">
  <header class="header-band">
    <div class="brand">
      <span class="brand__mark"></span>
      <span class="brand__name">BRAVURA GROUP</span>
    </div>
    <h1 class="cover-title">EASY TO UNDERSTAND AND READ<br>DIGITAL PHOTO REPORT</h1>
  </header>

  <div class="sheet sheet--back" aria-label="Sample report page with photo grid">
    <div class="sheet__bar"></div>
    <div class="photo-grid">
      <div class="photo-grid__cell"></div><div class="photo-grid__cell"></div><div class="photo-grid__cell"></div>
    </div>
    <div class="photo-grid__caption"></div>
    <div class="photo-grid" style="margin-top:4px">
      <div class="photo-grid__cell"></div><div class="photo-grid__cell"></div><div class="photo-grid__cell"></div>
    </div>
    <div class="photo-grid__caption"></div>
    <div class="photo-grid" style="margin-top:4px">
      <div class="photo-grid__cell"></div><div class="photo-grid__cell"></div><div class="photo-grid__cell"></div>
    </div>
  </div>

  <div class="sheet sheet--front" aria-label="Sample report page with notes and photos">
    <div class="sheet__bar"></div>
    <div class="text-lines"><span></span><span></span><span class="warn"></span><span class="warn"></span><span></span></div>
    <div class="photo-grid" style="grid-template-columns:repeat(3,1fr)">
      <div class="photo-grid__cell" style="background:linear-gradient(135deg,#555,#222)"></div>
      <div class="photo-grid__cell" style="background:linear-gradient(135deg,#777,#333)"></div>
      <div class="photo-grid__cell" style="background:linear-gradient(135deg,#999,#444)"></div>
    </div>
    <div class="photo-grid" style="margin-top:3px;grid-template-columns:1fr 2fr">
      <div class="photo-grid__cell" style="background:linear-gradient(135deg,#8e9a90,#4f5a52)"></div><div></div>
    </div>
    <div class="text-lines__head"></div>
    <div class="text-lines"><span></span><span></span><span></span></div>
    <div class="text-lines__head"></div>
    <div class="text-lines"><span></span><span></span></div>
    <div class="text-lines__head"></div>
    <div class="text-lines"><span></span><span class="warn"></span><span></span></div>
  </div>

  <div class="phone">
    <div class="phone__screen" role="img" aria-label="Inspection report cover with a house photo shown on a phone"></div>
    <div class="phone__button"></div>
  </div>

  <footer class="footer-band">
    <span class="footer-ring"></span>
    <span class="site-url">MORVANTEQ.COM</span>
  </footer>
</section>

<section class="page page--inspect">
  <header class="header-band">
    <div class="brand">
      <span class="brand__mark"></span>
      <span class="brand__name">BRAVURA GROUP</span>
    </div>
    <h2 class="inspect-title">WHAT WE INSPECT</h2>
    <p class="inspect-intro">A Commercial Inspection performed by The Bravura Group is based on the age, type and occupancy of the property. With over 500,000 properties inspected we know how to inspect each and every scenario. Our Inspections include the evaluation of all major components in a building, which establishes the components’ current condition, remaining design life, and any immediate and future repairs that are necessary.</p>
  </header>

  <div class="photo photo--wall" style="left:23px;top:202px;width:122px;height:104px;" role="img" aria-label="Inspector checking an electrical panel"></div>
  <div class="photo photo--meter" style="left:63px;top:283px;width:93px;height:82px;" role="img" aria-label="Hand holding an outlet tester"></div>

  <div class="photo photo--drain" style="left:184px;top:202px;width:122px;height:104px;" role="img" aria-label="Inspector examining a drainage grate"></div>
  <div class="photo photo--drain" style="left:232px;top:283px;width:94px;height:82px;" role="img" aria-label="Close view of a floor drain"></div>

  <div class="photo photo--thermal" style="left:343px;top:202px;width:121px;height:104px;" role="img" aria-label="Thermal camera scanning pipework"></div>
  <div class="photo photo--thermal" style="left:398px;top:292px;width:94px;height:82px;" role="img" aria-label="Thermal camera reading on a unit"></div>

  <h3 class="category-title" style="left:84px;top:385px;">PLUMBING</h3>
  <h3 class="category-title" style="left:258px;top:388px;">ROOF</h3>
  <h3 class="category-title" style="left:431px;top:388px;">FOUNDATION</h3>

  <div class="item-panel" style="left:24px;top:411px;width:121px;height:77px;"></div>
  <div class="item-panel" style="left:187px;top:411px;width:137px;height:77px;"></div>
  <div class="item-panel" style="left:369px;top:412px;width:120px;height:76px;"></div>

  <ul class="item-list item-list--plain" style="left:39px;top:415px;">
    <li>PANEL</li><li>OUTLETS</li><li>WIRING</li>
  </ul>
  <ul class="item-list item-list--dashed item-list--roof" style="left:203px;top:414px;">
    <li class="has-dash">DRAINAGE</li><li class="has-dash">GRADE</li><li class="has-dash">MOISTURE CONCRETE,</li><li>STEEL AND WOOD</li>
  </ul>
  <ul class="item-list item-list--dashed item-list--foundation" style="left:379px;top:418px;">
    <li class="has-dash">AIR CONDITION</li><li class="has-dash">HEATER</li><li class="has-dash">DUCTING</li>
  </ul>

  <footer class="footer-band">
    <span class="footer-ring"></span>
    <span class="site-url">MORVANTEQ.COM</span>
  </footer>
</section>

</body>
</html>
```